Brochure for dynamic theatrical production company

New brochure for Heron Stageworks, featuring our current theatrical projects. We are a theatrical producing and consulting company, and we need the brochure to communicate the breadth of our projects. Our work is produced and performed throughtout the United States and also tours to Europe, Asia, the Middle East and South America. We also work with companies and artists from around the globe and bring them to the United States to tour and develop new work. Projects range from experimental multi-disciplinary works to Broadway musicals.

The brochure is meant to introduce other performing arts professionals to our work. These potential clients might engage one of our artists or projects for a performance, or they may engage us as consultants on additional projects.

The final design should be a standard size document that is fairly simple and inexpensive to reproduce. This is a piece that is used within the entertainment industry to develop interest in our work from other theaters, presenters, festivals, donors and artists.

I have included the pdf of last year's design, as well as a word document with the text to be used for this year. The world document also contains a link to a dropbox folder with photos and other supplementary materials as well.

You can also refer to our website for insights into our work and our aesthetic. www.heronstageworks-example.com

Target Market(s)

Industry professionals, funders/investors, prospective clients.

Industry/Entity Type

Entertainment Industry

Font styles to use
Sans Serif

Colors

Designer to choose colors to be used in the design.

Requirements
Must have
• Please use text provided in "Heron Brochure 2018" document. A variety of photos and other graphics are available for download via a link embedded in the document.
• Please make sure the finished piece can be printed on standard paper sizes in the US: For example: ledger size is 279 x 432 mm (11.0 x 17.0 in), letter size is 216 x 279 mm (8.5 x 11.0 in), Legal size is 216 x 356 mm (8.5 x 14.0 in)
Nice to have
• Our previous brochure and current website use pictures in the shape of circles (see sample attached). I would like that to be consistent with the new brochure. Website, for your reference, is www.heronstageworks-example.com
Should not have
• non-standard paper sizes

```html
<!DOCTYPE html>
<html lang="en">
<head>
<meta charset="utf-8">
<title>Heron Brochure 2018 – Additional Programs</title>
<link href="https://fonts.googleapis.com/css2?family=Jost:wght@400;600&display=swap" rel="stylesheet">
<style>
  :root{
    --teal:#0aa0a8;
    --ink:#111111;
    --paper:#ffffff;
  }
  *{margin:0;padding:0;box-sizing:border-box}
  html,body{width:729px;height:1200px;overflow:hidden;background:var(--teal)}
  .page{position:relative;width:729px;height:1200px;background:var(--teal);overflow:hidden;
        font-family:"Jost",sans-serif;color:var(--paper)}
  .shapes{position:absolute;inset:0}
  .page-number{position:absolute;left:29px;top:23px;font-weight:600;font-size:14px;color:var(--paper)}
  .section-title{position:absolute;left:229px;width:250px;top:38px;text-align:center;
        font-weight:600;font-size:21px;line-height:29px;letter-spacing:.6px}
  .program-title{font-weight:600;font-size:22px;line-height:27px;letter-spacing:.6px}
  .program-subtitle{font-weight:600;font-size:14px;line-height:17px;letter-spacing:.2px}
  .body-copy{font-weight:400;font-size:12px;line-height:17.3px;letter-spacing:.15px}
  .body-copy p{margin-bottom:17.3px}
  .launchpad{position:absolute;left:43px;top:134px;width:206px}
  .launchpad .program-subtitle{margin-top:4px}
  .launchpad .body-copy{margin-top:36px}
  .makershub{position:absolute;left:260px;top:175px;width:212px}
  .makershub .hub-link{font-weight:600;font-size:16.5px;line-height:22px;text-decoration:underline;
        display:block;white-space:nowrap;letter-spacing:.3px}
  .makershub .body-copy{margin-top:38px}
  .body-copy .url{text-decoration:underline}
  .consulting{position:absolute;left:372px;top:826px;width:320px;color:var(--ink)}
  .consulting .body-copy{margin-top:28px;font-size:12.6px;line-height:17.6px}
  .client{position:absolute;font-size:13px;line-height:16px;color:var(--ink);font-weight:400}
</style>
</head>
<body>
<main class="page">
  <svg class="shapes" width="729" height="1200" viewBox="0 0 729 1200" aria-hidden="true">
    <circle cx="628" cy="1080" r="372" fill="var(--paper)"/>
    <circle cx="18" cy="10" r="102" fill="var(--paper)"/>
    <circle cx="18" cy="10" r="98" fill="var(--ink)"/>
  </svg>

  <div class="page-number">14</div>
  <h1 class="section-title">ADDITIONAL<br>PROGRAMS</h1>

  <section class="launchpad">
    <h2 class="program-title">PROJECT<br>LAUNCHPAD:</h2>
    <h3 class="program-subtitle">DEVELOPING DANCE<br>MUSICALS</h3>
    <div class="body-copy">
      <p>Designed to encourage collaborations in which choreography plays an integral part in the conception and creation of new musical projects, Project Launchpad provides a fully supported multi-week development residency for two creative teams in early conceptual stages of a new musical.</p>
      <p>The Launchpad Project was borne out of an extensive inquiry into the role that choreographers play in the conception and development of new musicals. Overwhelmingly, in the two-year study, we heard from directors, choreographers, composers, lyricists and book writers that while there is a genuine appetite for developing dance-driven musicals, there are limited avenues available to independent artists to develop these labor-intensive collaborations.</p>
      <p>It was out of these conversations that The Launchpad Project was created to 1) encourage creative teams to incorporate choreographic and directorial ideas at conception, 2) develop the work with dance fully integrated into the story-telling, and 3) address the existing financial and practical obstacles to developing those ideas in early stages of development.</p>
      <p>The Launchpad Project is sponsored through the leadership of The Marlow Ashby Foundation and with the generous support of The Corwin Hale Foundation, The Penrose Lyle Foundation, The Garrett Voss Foundation, The Delano Family Foundation, The Winifred Pell Trust.</p>
    </div>
  </section>

  <section class="makershub">
    <h2 class="program-subtitle">INTRODUCING</h2>
    <span class="hub-link">MAKERSHUB-EXAMPLE.ORG</span>
    <div class="body-copy">
      <p>We are pleased to introduce a new online community and resource. Still in nascent stages, makershub-example.org exists to create community among independent producers and makers of live performance for the purpose of sharing best practices, resources and building community. With our launch in January 2018, we invite producers, artists and supporters to join the community, and then we will work together to develop a robust forum that serves the needs of its members. For the latest updates and to sign up, visit <span class="url">www.makershub-example.org</span></p>
    </div>
  </section>

  <section class="consulting">
    <h2 class="program-title">HERON<br>CONSULTING</h2>
    <p class="body-copy">Since our formation, we have enjoyed numerous collaborations with artists and organizations as a consultant and advisor. Selected clients include:</p>
  </section>

  <ul class="clients" style="list-style:none">
    <li class="client" style="left:374px;top:1000px;width:80px">Larkspur Arts Center</li>
    <li class="client" style="left:474px;top:1000px;width:70px">Tangent Ensemble</li>
    <li class="client" style="left:552px;top:1000px;width:110px">Alder Hall Arts</li>
    <li class="client" style="left:372px;top:1066px;width:80px">Juniper Theater</li>
    <li class="client" style="left:468px;top:1066px;width:90px">Marlow Ashby Foundation</li>
  </ul>
</main>
</body>
</html>
```